Business card for medical clinic

I need an upmarket, modern medical/health business card for my clinic

Contact Information for Business Card

name, address, email, qr code

```html
<!DOCTYPE html>
<html lang="en">
<head>
<meta charset="utf-8">
<title>Alder Health Clinic – Business Card</title>
<link href="https://fonts.googleapis.com/css2?family=Cinzel:wght@600&family=Arimo:wght@400&display=swap" rel="stylesheet">
<style>
  :root {
    --backdrop: #d3d3d3;
    --card: #ffffff;
    --navy: #1d3a6b;
    --blue: #1a6fb0;
    --sky: #2aa6e0;
    --ink: #222222;
    --rule: #8cc2e4;
  }
  * { margin: 0; padding: 0; box-sizing: border-box; }
  html, body {
    width: 1200px; height: 915px; overflow: hidden;
    background: var(--backdrop);
  }
  .canvas { position: relative; width: 1200px; height: 915px; }
  .card {
    position: absolute;
    width: 630px; height: 360px;
    background: var(--card);
    border-radius: 24px;
    box-shadow: 0 6px 18px rgba(0,0,0,0.18);
    overflow: hidden;
  }
  .card--front { left: 60px; top: 60px; }
  .card--back { left: 510px; top: 495px; }

  .brand {
    display: flex; align-items: center;
    font-family: "Cinzel", serif; font-weight: 600;
    color: var(--blue);
    white-space: nowrap;
  }
  .brand__dot {
    border-radius: 50%;
    background: var(--sky);
    flex: none;
  }
  .card--front .brand {
    position: absolute; left: 50%; top: 50%;
    transform: translate(-50%, -50%);
    font-size: 34px; letter-spacing: 1px; gap: 14px;
  }
  .card--front .brand__dot { width: 26px; height: 26px; }

  .card--back .brand {
    position: absolute; left: 30px; top: 172px;
    width: 270px;
    font-size: 17px; letter-spacing: 0; gap: 10px;
  }
  .card--back .brand__dot { width: 14px; height: 14px; }

  .divider {
    position: absolute; left: 318px; top: 96px;
    width: 1px; height: 176px;
    background: var(--rule);
  }
  .contact {
    position: absolute; left: 342px; top: 96px;
    font-family: "Arimo", sans-serif; color: var(--ink);
    font-size: 14px; line-height: 1.3;
  }
  .contact__name {
    font-family: "Cinzel", serif; font-weight: 600;
    color: var(--blue); font-size: 22px; line-height: 1.1;
  }
  .contact__role { margin-bottom: 16px; }
  .contact__address { margin-bottom: 14px; }
  .contact__line { display: flex; align-items: center; gap: 8px; }
  .contact__icon { width: 12px; height: 12px; flex: none; fill: var(--sky); }
</style>
</head>
<body>
<main class="canvas">
  <section class="card card--front" aria-label="Card front">
    <div class="brand"><span class="brand__dot"></span>Alder Health Clinic</div>
  </section>

  <section class="card card--back" aria-label="Card back">
    <div class="brand"><span class="brand__dot"></span>Alder Health Clinic</div>
    <div class="divider"></div>
    <div class="contact">
      <div class="contact__name">Elena Marsh</div>
      <div class="contact__role">Director/Founder</div>
      <div class="contact__address">318 Harbor Lane<br>Westbrook NY 10542</div>
      <div class="contact__line">
        <svg class="contact__icon" viewBox="0 0 12 12" aria-hidden="true"><path d="M2.5 1 L4.5 1 L5.2 3.5 L4 4.4 Q5 6.8 7.6 8 L8.5 6.8 L11 7.5 L11 9.5 Q10.5 11 9 11 Q1 10 1 3 Q1 1.5 2.5 1 Z"/></svg>
        <span>0555 0142 387</span>
      </div>
      <div class="contact__line">
        <svg class="contact__icon" viewBox="0 0 12 12" aria-hidden="true"><path d="M1 2.5 H11 V9.5 H1 Z M1.6 3 L6 6.4 L10.4 3 Z" fill-rule="evenodd"/></svg>
        <span>info@alderhealthclinic.com</span>
      </div>
      <div class="contact__line">
        <svg class="contact__icon" viewBox="0 0 12 12" aria-hidden="true"><circle cx="6" cy="6" r="5"/><path d="M1 6 H11 M6 1 Q3 6 6 11 M6 1 Q9 6 6 11" stroke="#fff" stroke-width="0.8" fill="none"/></svg>
        <span>www.alderhealthclinic.com</span>
      </div>
    </div>
  </section>
</main>
</body>
</html>
```